Schlichtes Design für Malerbetrieb
Zielgruppe
Wir sind ein mittelgroßer Malerbetrieb in München mit umfangreichem Leistungsspektrum.
Unsere Hauptleistungen sind: Fassadenrenovierung, Altbausanierung, Betoninstandsetzung, Balkonabdichtung (kein Neubau!).
Unsere Zielgruppen sind: Hausverwaltungen, Firmen und Privatpersonen.
Unsere Kunden schätzen: Konstruktive Organisation und Planung im Vorfeld, Zuverlässigkeit, saubere Arbeitsweise, dauerhafte Balkonabdichtungen.
Aufgabenstellung
Wir möchten eine langlebige, stilvolle, minimalistische Homepage.
Wir möchten von der bestehenden Homepage nur die Schriftart für unseren Firmennamen (Century Gothic) und wenn möglich (nicht zwingend), irgendwo das florale Muster einbauen. Corporate-Design haben wir nicht.
Farbtöne: Firmennamen Orange (hellorange bis erdiges Orange möglich, da sind wir nicht fixiert) , einen dunklen Hintergrundfarbton (Petrol-Blaugrau ?) mit gelbem (neon bis senfgelb) Akzent (Linien), Blumenmuster weiß, grau.
Dies sind nur unsere Ideen. Wir sind aber auch absolut offen für eure Profi-Ideen.
Wir möchten uns von den unzähligen langweiligen 'Pinselseiten mit veralteten Bilder' unserer Kollegen interessant und mit Stil abheben.
Eher nach dem Motto 'weniger ist mehr'.
Einen positiven, sympathischen Eindruck geben und unsere Leistungen in den Vordergrund bringen.
Da wir viele Stammkunden haben, betreiben wir kein Social-Media und möchten dies vorerst auch nicht tun.
Die Seite wird in den nächsten Jahren nicht verändert, höchstens die Bilder aktualisiert.
Die Texte haben wir alle selbst entworfen und möchten wir so übernehmen.
Die Galerien sollen unkompliziert anzuschauen sein.
Uns gefällt die Struktur und Schlichtheit von https://vaartmolen.nl/ oder Timbra.de gut und wir mögen Vintage-Grafiken gerne.
Einerseits darf die Seite geradlinig, andererseits aber auch rund und floral wirken.

```html
<!DOCTYPE html>
<html lang="de">
<head>
<meta charset="utf-8">
<title>kolbrit Malerarbeiten</title>
<link rel="stylesheet" href="https://fonts.googleapis.com/css2?family=Encode+Sans+Condensed:wght@500&display=swap">
<style>
  :root {
    --bar: #3a393b;
    --backdrop: #403f42;
    --petrol: #023f53;
    --amber: #f7b231;
    --stone: #9d9ea0;
    --white: #ffffff;
  }
  * { margin: 0; padding: 0; box-sizing: border-box; }
  html, body { width: 1200px; height: 900px; overflow: hidden; background: var(--backdrop); }
  .page { position: relative; width: 1200px; height: 900px; overflow: hidden; }
  .stage { position: absolute; inset: 0; width: 1200px; height: 900px; display: block; }
  .top-bar {
    position: absolute; left: 0; top: 0; width: 1200px; height: 127px;
    background: var(--bar);
  }
  .top-brand {
    position: absolute; right: 48px; top: 22px;
    font-family: "Encode Sans Condensed", sans-serif;
    font-size: 44px; font-weight: 500; line-height: 1; color: var(--amber);
  }
  .main-nav {
    position: absolute; right: 50px; top: 90px;
    display: flex; gap: 20px;
    font-family: "Encode Sans Condensed", sans-serif;
    font-size: 24px; font-weight: 500; color: var(--white); line-height: 1;
  }
  .hero-name {
    position: absolute; left: 120px; top: 360px;
    font-family: "Encode Sans Condensed", sans-serif;
    font-size: 118px; font-weight: 500; line-height: 1; color: var(--amber);
  }
  .bottom-bar {
    position: absolute; left: 0; top: 840px; width: 1200px; height: 60px;
    background: var(--bar);
  }
  .legal-nav {
    position: absolute; right: 16px; top: 17px;
    display: flex; gap: 24px;
    font-family: "Encode Sans Condensed", sans-serif;
    font-size: 26px; font-weight: 500; color: var(--white); line-height: 1;
  }
</style>
</head>
<body>
<div class="page">
  <svg class="stage" viewBox="0 0 1024 768">
    <rect class="floral-field" x="0" y="108" width="1024" height="610" fill="var(--backdrop)" role="img" aria-label="Dezentes florales Damastmuster in Grautönen"/>
    <polygon class="petrol-wedge" points="0,108 222,108 730,355 278,580 0,447" fill="var(--petrol)"/>
    <polygon class="stone-wedge" points="0,447 0,718 552,718" fill="var(--stone)"/>
    <polygon class="amber-wedge" points="1024,213 512,463 1024,714" fill="var(--amber)"/>
  </svg>

  <header class="top-bar">
    <div class="top-brand">kolbrit</div>
    <nav class="main-nav">
      <span>malerarbeiten</span>
      <span>betoninstandsetzung</span>
      <span>balkonabdichtung</span>
      <span>farbgestaltung</span>
      <span>wärmedämmung</span>
      <span>ausbildung</span>
      <span>portrait</span>
    </nav>
  </header>

  <div class="hero-name">kolbrit</div>

  <footer class="bottom-bar">
    <nav class="legal-nav">
      <span>Kontakt</span>
      <span>Impressum</span>
      <span>Datenschutz</span>
    </nav>
  </footer>
</div>
</body>
</html>
```